Fun A1 2012 family planner using clever typography and block colour

I have been looking for an A1 2012 family planner and I have not been able to find one. Hence I would like help to develop such a planner. I plan to print it on matt paper, portrait orientated. I have attached some reference pictures of our 2011 planner. I like interesting typography, clear clean colours and simple illustration. I need space to write in daily events and need the weeks and days to be clearly delineated from each other. Each day cell needs the date and day in it (please refer to the file uploaded for a visual reference confirming this). Each weekend needs some kind of colour/ typographic delineation. I want a design for a year-at-a-view calendar. I plan to print the planner in Sydney, Australia with brightloomprints.com.au and probably to sell printed copies online. The terms & conditions of this project are that I will own the design concept 100% and in perpetuity worldwide once payment has been made. (NB. The attached Work File in Word contains a rough layout and all months, days and dates all typed up to make for quicker design.)

Target Market(s)

Reasonably well heeled family of 4. 2 parents. 2 kids. 2 pets.

Industry/Entity Type

Events

Requirements
Must have
• The calendar must be portrait (not landscape orientated), A1 size. It will be printed on matt paper by brightloomprints.com.au. It must have months running left to right (Jan-Dec) and day/date cells running top to bottom (refer 2011 planner photos in file uploaded). The day/ date cells must be around 3(w)x2(h)cm - big enough to write daily events in. Weekends must be colour/ typographically delineated. 2012 year must be noted as must "A Pebblegate Inc Project" and web address in fine print bottom left hand left hand corner.
Nice to have
• A Pebblegate Inc logo in bottom left hand corder (perhaps Nimble Owl like: http://www.artmarketly.com/design_submission.aspx?designid=731462). Header/Footer space for customisation (e.g. "Hartono-Quist 2012 Planner" or "XYZ Co 2012 Planner".
Should not have
• The calendar should not use photographs or resemble standard or cheesy wall calendars. No watermarks please.

```html
<!DOCTYPE html>
<html lang="en">
<head>
<meta charset="utf-8">
<title>XYZ Co 2012 Planner</title>
<link href="https://fonts.googleapis.com/css2?family=Quicksand:wght@500;700&display=swap" rel="stylesheet">
<style>
:root{
  --ink:#58595b;
  --jan-c:#fff07a;--jan-d:#f9b233;--jan-l:#fef8cc;--jan-h:#fff07d;--jan-t:#f7941d;
  --feb-c:#5bc8f0;--feb-d:#2aa6dc;--feb-l:#e4f5fc;--feb-h:#c7ebfa;--feb-t:#29abe2;
  --mar-c:#f59bc4;--mar-d:#e85a9e;--mar-l:#fdeaf2;--mar-h:#fbd2e4;--mar-t:#ec5a9e;
  --apr-c:#fcb46b;--apr-d:#f7931e;--apr-l:#feefde;--apr-h:#fdd6af;--apr-t:#f7931e;
  --may-c:#b9dc8f;--may-d:#7bb546;--may-l:#eff7e6;--may-h:#d8ecc0;--may-t:#7ab648;
  --jun-c:#b893c7;--jun-d:#8e5ba6;--jun-l:#f6f1f8;--jun-h:#e8dcee;--jun-t:#9556a8;
  --foot-blue:#4fc8f0;--foot-yellow:#fff200;--foot-pink:#f7b8d6;
}
*{box-sizing:border-box;margin:0;padding:0}
html,body{width:847px;height:1200px;overflow:hidden;background:#fff}
.sheet{position:relative;width:847px;height:1200px;font-family:"Quicksand",sans-serif;color:var(--ink)}
.year{position:absolute;left:30px;top:32px;display:grid;grid-template-columns:repeat(12,63.5px);column-gap:2.2px}
.month .tab{height:46px;border-radius:7px 7px 5px 5px;background:linear-gradient(var(--c) 0 40px,var(--d) 40px);color:#fff;font-weight:700;font-size:25px;letter-spacing:-0.5px;text-align:center;line-height:42px;margin-bottom:4px}
.month p{height:31.3px;margin-bottom:2.2px;border-radius:4px;background:var(--l);padding:3px 0 0 6px;font-size:8px;line-height:8px;font-weight:500}
.month p b{display:block;font-size:15px;line-height:14px;font-weight:700}
.month p.we{background:var(--h);color:var(--t)}
.jan{--c:var(--jan-c);--d:var(--jan-d);--l:var(--jan-l);--h:var(--jan-h);--t:var(--jan-t)}
.feb,.aug{--c:var(--feb-c);--d:var(--feb-d);--l:var(--feb-l);--h:var(--feb-h);--t:var(--feb-t)}
.mar,.sep{--c:var(--mar-c);--d:var(--mar-d);--l:var(--mar-l);--h:var(--mar-h);--t:var(--mar-t)}
.apr,.oct{--c:var(--apr-c);--d:var(--apr-d);--l:var(--apr-l);--h:var(--apr-h);--t:var(--apr-t)}
.may,.nov{--c:var(--may-c);--d:var(--may-d);--l:var(--may-l);--h:var(--may-h);--t:var(--may-t)}
.jun,.dec{--c:var(--jun-c);--d:var(--jun-d);--l:var(--jun-l);--h:var(--jun-h);--t:var(--jun-t)}
.jul{--c:var(--jan-c);--d:var(--jan-d);--l:var(--jan-l);--h:var(--jan-h);--t:var(--jan-t)}
.title{position:absolute;left:30px;top:1130px;font-weight:700;font-size:45px;letter-spacing:0.5px;line-height:50px}
.title .co{color:var(--foot-blue)}.title .yr{color:var(--foot-yellow)}.title .pl{color:var(--foot-pink)}
</style>
</head>
<body>
<div class="sheet">
<div class="year">

<section class="month jan"><div class="tab">JAN</div>
<p class="we"><b>01</b>Sun</p><p><b>02</b>Mon</p><p><b>03</b>Tue</p><p><b>02</b>Thu</p><p><b>05</b>Thu</p><p><b>06</b>Fri</p><p class="we"><b>07</b>Sat</p>
<p class="we"><b>08</b>Sun</p><p><b>09</b>Mon</p><p><b>10</b>Tue</p><p><b>02</b>Thu</p><p><b>12</b>Thu</p><p><b>13</b>Fri</p><p class="we"><b>14</b>Sat</p>
<p class="we"><b>15</b>Sun</p><p><b>16</b>Mon</p><p><b>17</b>Tue</p><p><b>02</b>Thu</p><p><b>19</b>Thu</p><p><b>20</b>Fri</p><p class="we"><b>21</b>Sat</p>
<p class="we"><b>22</b>Sun</p><p><b>23</b>Mon</p><p><b>24</b>Tue</p><p><b>02</b>Thu</p><p><b>26</b>Thu</p><p><b>27</b>Fri</p><p class="we"><b>28</b>Sat</p>
<p class="we"><b>29</b>Sun</p><p><b>30</b>Mon</p><p><b>31</b>Tue</p>
</section>

<section class="month feb"><div class="tab">FEB</div>
<p><b>01</b>Wed</p><p><b>02</b>Thu</p><p><b>01</b>Wed</p><p class="we"><b>02</b>Thu</p><p class="we"><b>01</b>Wed</p><p><b>02</b>Thu</p><p><b>01</b>Wed</p>
<p><b>01</b>Wed</p><p><b>02</b>Thu</p><p><b>01</b>Wed</p><p class="we"><b>02</b>Thu</p><p class="we"><b>01</b>Wed</p><p><b>02</b>Thu</p><p><b>01</b>Wed</p>
<p><b>01</b>Wed</p><p><b>02</b>Thu</p><p><b>01</b>Wed</p><p class="we"><b>02</b>Thu</p><p class="we"><b>01</b>Wed</p><p><b>02</b>Thu</p><p><b>01</b>Wed</p>
<p><b>01</b>Wed</p><p><b>02</b>Thu</p><p><b>01</b>Wed</p><p class="we"><b>02</b>Thu</p><p class="we"><b>01</b>Wed</p><p><b>02</b>Thu</p><p><b>01</b>Wed</p>
<p><b>01</b>Wed</p><p><b>02</b>Thu</p><p><b>01</b>Wed</p>
</section>

<section class="month mar"><div class="tab">MAR</div>
<p><b>01</b>Thu</p><p><b>02</b>Fri</p><p class="we"><b>01</b>Thu</p><p class="we"><b>02</b>Fri</p><p><b>01</b>Thu</p><p><b>02</b>Fri</p><p><b>01</b>Thu</p>
<p><b>01</b>Thu</p><p><b>02</b>Fri</p><p class="we"><b>01</b>Thu</p><p class="we"><b>02</b>Fri</p><p><b>01</b>Thu</p><p><b>02</b>Fri</p><p><b>01</b>Thu</p>
<p><b>01</b>Thu</p><p><b>02</b>Fri</p><p class="we"><b>01</b>Thu</p><p class="we"><b>02</b>Fri</p><p><b>01</b>Thu</p><p><b>02</b>Fri</p><p><b>01</b>Thu</p>
<p><b>01</b>Thu</p><p><b>02</b>Fri</p><p class="we"><b>01</b>Thu</p><p class="we"><b>02</b>Fri</p><p><b>01</b>Thu</p><p><b>02</b>Fri</p><p><b>01</b>Thu</p>
<p><b>01</b>Thu</p><p><b>02</b>Fri</p><p class="we"><b>01</b>Thu</p>
</section>

<section class="month apr"><div class="tab">APR</div>
<p class="we"><b>01</b>Sun</p><p><b>02</b>Mon</p><p><b>01</b>Sun</p><p><b>02</b>Mon</p><p><b>01</b>Sun</p><p><b>02</b>Mon</p><p class="we"><b>01</b>Sun</p>
<p class="we"><b>01</b>Sun</p><p><b>02</b>Mon</p><p><b>01</b>Sun</p><p><b>02</b>Mon</p><p><b>01</b>Sun</p><p><b>02</b>Mon</p><p class="we"><b>01</b>Sun</p>
<p class="we"><b>01</b>Sun</p><p><b>02</b>Mon</p><p><b>01</b>Sun</p><p><b>02</b>Mon</p><p><b>01</b>Sun</p><p><b>02</b>Mon</p><p class="we"><b>01</b>Sun</p>
<p class="we"><b>01</b>Sun</p><p><b>02</b>Mon</p><p><b>01</b>Sun</p><p><b>02</b>Mon</p><p><b>01</b>Sun</p><p><b>02</b>Mon</p><p class="we"><b>01</b>Sun</p>
<p class="we"><b>01</b>Sun</p><p><b>02</b>Mon</p><p><b>01</b>Sun</p>
</section>

<section class="month may"><div class="tab">MAY</div>
<p><b>01</b>Tue</p><p><b>02</b>Wed</p><p><b>01</b>Tue</p><p><b>02</b>Wed</p><p class="we"><b>01</b>Tue</p><p class="we"><b>02</b>Wed</p><p><b>01</b>Tue</p>
<p><b>01</b>Tue</p><p><b>02</b>Wed</p><p><b>01</b>Tue</p><p><b>02</b>Wed</p><p class="we"><b>01</b>Tue</p><p class="we"><b>02</b>Wed</p><p><b>01</b>Tue</p>
<p><b>01</b>Tue</p><p><b>02</b>Wed</p><p><b>01</b>Tue</p><p><b>02</b>Wed</p><p class="we"><b>01</b>Tue</p><p class="we"><b>02</b>Wed</p><p><b>01</b>Tue</p>
<p><b>01</b>Tue</p><p><b>02</b>Wed</p><p><b>01</b>Tue</p><p><b>02</b>Wed</p><p class="we"><b>01</b>Tue</p><p class="we"><b>02</b>Wed</p><p><b>01</b>Tue</p>
<p><b>01</b>Tue</p><p><b>02</b>Wed</p><p><b>01</b>Tue</p>
</section>

<section class="month jun"><div class="tab">JUN</div>
<p><b>01</b>Fri</p><p class="we"><b>02</b>Sat</p><p class="we"><b>01</b>Fri</p><p><b>02</b>Sat</p><p><b>01</b>Fri</p><p><b>02</b>Sat</p><p><b>01</b>Fri</p>
<p><b>01</b>Fri</p><p class="we"><b>02</b>Sat</p><p class="we"><b>01</b>Fri</p><p><b>02</b>Sat</p><p><b>01</b>Fri</p><p><b>02</b>Sat</p><p><b>01</b>Fri</p>
<p><b>01</b>Fri</p><p class="we"><b>02</b>Sat</p><p class="we"><b>01</b>Fri</p><p><b>02</b>Sat</p><p><b>01</b>Fri</p><p><b>02</b>Sat</p><p><b>01</b>Fri</p>
<p><b>01</b>Fri</p><p class="we"><b>02</b>Sat</p><p class="we"><b>01</b>Fri</p><p><b>02</b>Sat</p><p><b>01</b>Fri</p><p><b>02</b>Sat</p><p><b>01</b>Fri</p>
<p><b>01</b>Fri</p><p class="we"><b>02</b>Sat</p><p class="we"><b>01</b>Fri</p>
</section>

<section class="month jul"><div class="tab">JUL</div>
<p class="we"><b>01</b>Sun</p><p><b>02</b>Mon</p><p><b>01</b>Sun</p><p><b>02</b>Mon</p><p><b>01</b>Sun</p><p><b>02</b>Mon</p><p class="we"><b>01</b>Sun</p>
<p class="we"><b>01</b>Sun</p><p><b>02</b>Mon</p><p><b>01</b>Sun</p><p><b>02</b>Mon</p><p><b>01</b>Sun</p><p><b>02</b>Mon</p><p class="we"><b>01</b>Sun</p>
<p class="we"><b>01</b>Sun</p><p><b>02</b>Mon</p><p><b>01</b>Sun</p><p><b>02</b>Mon</p><p><b>01</b>Sun</p><p><b>02</b>Mon</p><p class="we"><b>01</b>Sun</p>
<p class="we"><b>01</b>Sun</p><p><b>02</b>Mon</p><p><b>01</b>Sun</p><p><b>02</b>Mon</p><p><b>01</b>Sun</p><p><b>02</b>Mon</p><p class="we"><b>01</b>Sun</p>
<p class="we"><b>01</b>Sun</p><p><b>02</b>Mon</p><p><b>01</b>Sun</p>
</section>

<section class="month aug"><div class="tab">AUG</div>
<p><b>01</b>Wed</p><p><b>02</b>Thu</p><p><b>01</b>Wed</p><p><b>02</b>Thu</p><p><b>01</b>Wed</p><p><b>02</b>Thu</p><p><b>01</b>Wed</p>
<p><b>01</b>Wed</p><p><b>02</b>Thu</p><p><b>01</b>Wed</p><p><b>02</b>Thu</p><p><b>01</b>Wed</p><p><b>02</b>Thu</p><p><b>01</b>Wed</p>
<p><b>01</b>Wed</p><p><b>02</b>Thu</p><p><b>01</b>Wed</p><p><b>02</b>Thu</p><p><b>01</b>Wed</p><p><b>02</b>Thu</p><p><b>01</b>Wed</p>
<p><b>01</b>Wed</p><p><b>02</b>Thu</p><p><b>01</b>Wed</p><p><b>02</b>Thu</p><p><b>01</b>Wed</p><p><b>02</b>Thu</p><p><b>01</b>Wed</p>
<p><b>01</b>Wed</p><p><b>02</b>Thu</p><p><b>01</b>Wed</p>
</section>

<section class="month sep"><div class="tab">SEP</div>
<p><b>01</b>Sat</p><p><b>02</b>Sun</p><p><b>01</b>Sat</p><p><b>02</b>Sun</p><p><b>01</b>Sat</p><p><b>02</b>Sun</p><p><b>01</b>Sat</p>
<p><b>01</b>Sat</p><p><b>02</b>Sun</p><p><b>01</b>Sat</p><p><b>02</b>Sun</p><p><b>01</b>Sat</p><p><b>02</b>Sun</p><p><b>01</b>Sat</p>
<p><b>01</b>Sat</p><p><b>02</b>Sun</p><p><b>01</b>Sat</p><p><b>02</b>Sun</p><p><b>01</b>Sat</p><p><b>02</b>Sun</p><p><b>01</b>Sat</p>
<p><b>01</b>Sat</p><p><b>02</b>Sun</p><p><b>01</b>Sat</p><p><b>02</b>Sun</p><p><b>01</b>Sat</p><p><b>02</b>Sun</p><p><b>01</b>Sat</p>
<p><b>01</b>Sat</p><p><b>02</b>Sun</p><p><b>01</b>Sat</p>
</section>

<section class="month oct"><div class="tab">OCT</div>
<p><b>01</b>Mon</p><p><b>02</b>Tue</p><p><b>01</b>Mon</p><p><b>02</b>Tue</p><p><b>01</b>Mon</p><p><b>02</b>Tue</p><p><b>01</b>Mon</p>
<p><b>01</b>Mon</p><p><b>02</b>Tue</p><p><b>01</b>Mon</p><p><b>02</b>Tue</p><p><b>01</b>Mon</p><p><b>02</b>Tue</p><p><b>01</b>Mon</p>
<p><b>01</b>Mon</p><p><b>02</b>Tue</p><p><b>01</b>Mon</p><p><b>02</b>Tue</p><p><b>01</b>Mon</p><p><b>02</b>Tue</p><p><b>01</b>Mon</p>
<p><b>01</b>Mon</p><p><b>02</b>Tue</p><p><b>01</b>Mon</p><p><b>02</b>Tue</p><p><b>01</b>Mon</p><p><b>02</b>Tue</p><p><b>01</b>Mon</p>
<p><b>01</b>Mon</p><p><b>02</b>Tue</p><p><b>01</b>Mon</p>
</section>

<section class="month nov"><div class="tab">NOV</div>
<p><b>01</b>Thu</p><p><b>02</b>Fri</p><p><b>01</b>Thu</p><p><b>02</b>Fri</p><p><b>01</b>Thu</p><p><b>02</b>Fri</p><p><b>01</b>Thu</p>
<p><b>01</b>Thu</p><p><b>02</b>Fri</p><p><b>01</b>Thu</p><p><b>02</b>Fri</p><p><b>01</b>Thu</p><p><b>02</b>Fri</p><p><b>01</b>Thu</p>
<p><b>01</b>Thu</p><p><b>02</b>Fri</p><p><b>01</b>Thu</p><p><b>02</b>Fri</p><p><b>01</b>Thu</p><p><b>02</b>Fri</p><p><b>01</b>Thu</p>
<p><b>01</b>Thu</p><p><b>02</b>Fri</p><p><b>01</b>Thu</p><p><b>02</b>Fri</p><p><b>01</b>Thu</p><p><b>02</b>Fri</p><p><b>01</b>Thu</p>
<p><b>01</b>Thu</p><p><b>02</b>Fri</p><p><b>01</b>Thu</p>
</section>

<section class="month dec"><div class="tab">DEC</div>
<p><b>01</b>Sat</p><p><b>02</b>Sun</p><p><b>01</b>Sat</p><p><b>02</b>Sun</p><p><b>01</b>Sat</p><p><b>02</b>Sun</p><p><b>01</b>Sat</p>
<p><b>01</b>Sat</p><p><b>02</b>Sun</p><p><b>01</b>Sat</p><p><b>02</b>Sun</p><p><b>01</b>Sat</p><p><b>02</b>Sun</p><p><b>01</b>Sat</p>
<p><b>01</b>Sat</p><p><b>02</b>Sun</p><p><b>01</b>Sat</p><p><b>02</b>Sun</p><p><b>01</b>Sat</p><p><b>02</b>Sun</p><p><b>01</b>Sat</p>
<p><b>01</b>Sat</p><p><b>02</b>Sun</p><p><b>01</b>Sat</p><p><b>02</b>Sun</p><p><b>01</b>Sat</p><p><b>02</b>Sun</p><p><b>01</b>Sat</p>
<p><b>01</b>Sat</p><p><b>02</b>Sun</p><p><b>01</b>Sat</p>
</section>

</div>
<h1 class="title"><span class="co">XYZ CO</span> <span class="yr">2012</span> <span class="pl">PLANNER</span></h1>
</div>
</body>
</html>
```